Mobile Friendly Lead Generation Landing Page

We are a web marketing company that specialized in web lead generation. Recently we have started buying media from mobile devices and we need a mobile interface(landing page) where we can collect user data in an effective manner.

Our current mobile landing page is:
http://www.tutorpath.example.com/lp13d/index.aspx?a=true&source=841356
Through this you can see what the steps/questions users need to answer to get matched to a school. We need the design for the whole process.

We are pretty open for design ideas and our goal is to make this mobile optimized landing page have the look and feel of an app...but not an app.
There are several questions in the process but we are open to changing the way they are presented. As in, you can have one question at a time or a few.
The goal is to make this EXTREMELY EASY for users to interact with.

One example that we have liked is:
http://learnvane.example/schools/57214-page1.lvne (please note that this opens only on mobile devices)

Some of these screenshots are attached.

Our web form looks like this:
http://www.tutorpath.example.com/lp88/index.aspx?a=true

```html
<!DOCTYPE html>
<html lang="en">
<head>
<meta charset="utf-8">
<title>Mobile Lead Form – Main Screen Revisions</title>
<link rel="stylesheet" href="https://fonts.googleapis.com/css2?family=Roboto:wght@300;400;500;700&family=Roboto+Condensed:wght@400&display=swap">
<style>
  :root {
    --page-bg: #eef4f0;
    --sky: #12a2f2;
    --sky-field: #8fd5fa;
    --sky-pale: #bfe3f6;
    --signal-red: #e8161b;
    --sun-yellow: #f8c500;
    --toolbar-blue: #1565f5;
    --go-green: #1db51d;
    --ink: #2b2b2b;
    --ink-soft: #3d3d3d;
    --accent-blue: #1a5ff0;
    --rule: #dcdcdc;
    --dot: #c4c4c4;
    --topic-art: #f0157a;
    --topic-business: #12b52a;
    --topic-justice: #e8141b;
    --topic-education: #1a5ff0;
    --topic-engineering: #f57a10;
    --topic-other: #111111;
  }
  * { box-sizing: border-box; margin: 0; padding: 0; }
  html, body { width: 1200px; height: 840px; overflow: hidden; }
  body { position: relative; background: var(--page-bg); font-family: "Roboto", Arial, sans-serif; color: var(--ink); }

  .screen { position: absolute; top: 127px; width: 300px; height: 540px; overflow: hidden; background: var(--sky-pale); box-shadow: 0 0 0 1px rgba(0,0,0,.08); }
  .screen--rev2 { left: 212px; }
  .screen--rev3 { left: 672px; }

  .status-bar { position: relative; height: 22px; background: var(--sky); color: #fff; font-size: 11px; display: flex; align-items: center; justify-content: space-between; padding: 0 6px; }
  .status-carrier { display: flex; align-items: center; gap: 4px; }
  .status-signal { letter-spacing: -1px; font-size: 8px; }
  .status-time { position: absolute; left: 0; right: 0; text-align: center; font-weight: 500; pointer-events: none; }
  .status-battery { display: flex; align-items: center; gap: 4px; }

  .address-bar { height: 41px; background: var(--sky); padding: 8px 9px 7px; }
  .address-field { position: relative; height: 26px; background: var(--sky-field); border-radius: 4px; color: #fff; font-size: 14px; line-height: 26px; text-align: center; }
  .address-reload { position: absolute; right: 6px; top: 4px; }

  .banner { background: var(--signal-red); color: #fff; text-align: center; }
  .banner--headline { margin-top: 19px; height: 38px; line-height: 38px; font-size: 19px; font-weight: 300; }
  .banner--headline strong { font-weight: 700; }
  .banner--prompt { height: 42px; line-height: 42px; font-family: "Roboto Condensed", "Arial Narrow", sans-serif; font-size: 17px; text-transform: uppercase; }

  .hero { position: relative; height: 124px; }
  .grant-badge { position: absolute; left: 50px; top: 22px; width: 200px; height: 60px; border-radius: 8px; background: var(--sun-yellow); display: flex; align-items: center; justify-content: center; text-align: center; font-size: 12.5px; line-height: 15px; color: var(--ink); }
  .hero-prompt { position: absolute; left: 14px; bottom: 8px; font-size: 13px; color: var(--ink); }

  .grant-strip { margin-top: 3px; height: 29px; background: var(--sun-yellow); position: relative; font-family: "Roboto Condensed", "Arial Narrow", sans-serif; font-size: 12.5px; line-height: 29px; text-align: center; color: var(--ink-soft); }
  .grant-strip::before, .grant-strip::after { content: ""; position: absolute; left: 0; right: 0; border-top: 1px dashed #fff; }
  .grant-strip::before { top: 3px; }
  .grant-strip::after { bottom: 3px; }

  .intro { height: 88px; display: flex; align-items: center; justify-content: center; font-size: 18px; font-weight: 400; color: #1d1d1d; }
  .intro em { font-style: normal; color: var(--accent-blue); }

  .dot-rule { height: 19px; background: #fff; background-image: radial-gradient(circle, var(--dot) 1.3px, transparent 1.6px); background-size: 8px 19px; background-position: 1px 0; }

  .topics { list-style: none; background: #fff; }
  .topic { height: 41px; display: flex; align-items: center; padding: 0 10px 0 7px; border-top: 1px solid var(--rule); font-size: 13px; color: var(--ink-soft); }
  .topic:first-child { border-top: none; }
  .screen--rev3 .topic { font-family: "Roboto Condensed", "Arial Narrow", sans-serif; font-size: 14px; }
  .topic-icon { width: 32px; height: 32px; border-radius: 6px; display: flex; align-items: center; justify-content: center; margin-right: 8px; flex-shrink: 0; }
  .topic-icon--round { border-radius: 50%; }
  .topic-icon--art { background: var(--topic-art); }
  .topic-icon--business { background: var(--topic-business); }
  .topic-icon--justice { background: var(--topic-justice); }
  .topic-icon--education { background: var(--topic-education); }
  .topic-icon--engineering { background: var(--topic-engineering); }
  .topic-icon--other { background: var(--topic-other); }
  .topic-label { flex: 1; }
  .topic-go { width: 19px; height: 19px; border-radius: 50%; background: var(--go-green); display: flex; align-items: center; justify-content: center; }

  .toolbar { position: absolute; left: 0; right: 0; bottom: 0; height: 50px; background: var(--toolbar-blue); display: flex; justify-content: space-around; align-items: center; padding: 0 6px; }

  .caption { position: absolute; top: 786px; width: 400px; text-align: center; font-size: 27px; font-weight: 400; color: #222; }
  .caption--rev2 { left: 162px; }
  .caption--rev3 { left: 622px; }
</style>
</head>
<body>

<section class="screen screen--rev2" aria-label="Main screen, revision 2">
  <div class="status-bar">
    <span class="status-carrier"><span class="status-signal">●●●○○</span> Brightwave
      <svg width="12" height="9" viewBox="0 0 12 9"><path d="M1 3.2a7 7 0 0 1 10 0M2.8 5a4.5 4.5 0 0 1 6.4 0" stroke="#fff" stroke-width="1.3" fill="none"/><circle cx="6" cy="7.4" r="1.2" fill="#fff"/></svg>
    </span>
    <span class="status-time">4:21 PM</span>
    <span class="status-battery">100%
      <svg width="24" height="10" viewBox="0 0 24 10"><rect x=".5" y=".5" width="20" height="9" rx="2" fill="none" stroke="#fff"/><rect x="2" y="2" width="17" height="6" rx="1" fill="#fff"/><rect x="21.5" y="3" width="2" height="4" rx="1" fill="#fff"/></svg>
    </span>
  </div>
  <div class="address-bar">
    <div class="address-field">www.tutorpath.example.com
      <svg class="address-reload" width="18" height="18" viewBox="0 0 18 18"><path d="M14 9a5 5 0 1 1-1.5-3.6" stroke="#fff" stroke-width="1.4" fill="none"/><path d="M13.5 2.5v3.5H10" stroke="#fff" stroke-width="1.4" fill="none"/></svg>
    </div>
  </div>

  <div class="banner banner--headline">Complete our <strong>3 minute</strong> App!</div>

  <div class="hero">
    <p class="grant-badge">Get up to $5, 645* per year<br>in Grants if you qualify</p>
    <p class="hero-prompt">Please select Area of Interest:</p>
  </div>

  <ul class="topics">
    <li class="topic"><span class="topic-icon topic-icon--art"><svg width="18" height="18" viewBox="0 0 18 18"><path d="M14 2 7 10M5 11c-2 1-2 3-3 5 2-1 4-1 5-3" stroke="#fff" stroke-width="1.4" fill="none"/></svg></span><span class="topic-label">Art &amp; Design</span><span class="topic-go"><svg width="8" height="10" viewBox="0 0 8 10"><path d="M2 1l4 4-4 4" stroke="#fff" stroke-width="2" fill="none"/></svg></span></li>
    <li class="topic"><span class="topic-icon topic-icon--business"><svg width="20" height="18" viewBox="0 0 20 18"><rect x="2" y="5" width="16" height="11" rx="1" stroke="#fff" stroke-width="1.4" fill="none"/><path d="M7 5V3h6v2M2 9h16" stroke="#fff" stroke-width="1.4" fill="none"/></svg></span><span class="topic-label">Business</span><span class="topic-go"><svg width="8" height="10" viewBox="0 0 8 10"><path d="M2 1l4 4-4 4" stroke="#fff" stroke-width="2" fill="none"/></svg></span></li>
    <li class="topic"><span class="topic-icon topic-icon--justice"><svg width="20" height="20" viewBox="0 0 20 20"><rect x="6" y="2" width="10" height="5" transform="rotate(35 11 4.5)" fill="#fff"/><path d="M9 8 3 15" stroke="#fff" stroke-width="2"/><path d="M10 18h8" stroke="#fff" stroke-width="2"/></svg></span><span class="topic-label">Criminal Justice</span><span class="topic-go"><svg width="8" height="10" viewBox="0 0 8 10"><path d="M2 1l4 4-4 4" stroke="#fff" stroke-width="2" fill="none"/></svg></span></li>
    <li class="topic"><span class="topic-icon topic-icon--education"><svg width="26" height="22" viewBox="0 0 26 22"><text x="13" y="9" text-anchor="middle" font-family="Roboto, sans-serif" font-size="9" fill="#fff">ABC</text><path d="M4 11h18" stroke="#fff"/><text x="13" y="20" text-anchor="middle" font-family="Roboto, sans-serif" font-size="9" fill="#fff">1 2 3</text></svg></span><span class="topic-label">Education &amp; Teaching</span><span class="topic-go"><svg width="8" height="10" viewBox="0 0 8 10"><path d="M2 1l4 4-4 4" stroke="#fff" stroke-width="2" fill="none"/></svg></span></li>
    <li class="topic"><span class="topic-icon topic-icon--engineering"><svg width="20" height="20" viewBox="0 0 20 20"><circle cx="10" cy="3" r="1.6" stroke="#fff" fill="none"/><path d="M9 4.5 4 18M11 4.5 16 18M5.5 12h9" stroke="#fff" stroke-width="1.4" fill="none"/></svg></span><span class="topic-label">Engineering</span><span class="topic-go"><svg width="8" height="10" viewBox="0 0 8 10"><path d="M2 1l4 4-4 4" stroke="#fff" stroke-width="2" fill="none"/></svg></span></li>
    <li class="topic"><span class="topic-icon topic-icon--other"><svg width="22" height="18" viewBox="0 0 22 18"><path d="M11 4C8 2 5 2 2 3v11c3-1 6-1 9 1 3-2 6-2 9-1V3c-3-1-6-1-9 1zM11 4v11" stroke="#fff" stroke-width="1.3" fill="none"/></svg></span><span class="topic-label">Other</span><span class="topic-go"><svg width="8" height="10" viewBox="0 0 8 10"><path d="M2 1l4 4-4 4" stroke="#fff" stroke-width="2" fill="none"/></svg></span></li>
  </ul>

  <nav class="toolbar" aria-label="Browser toolbar">
    <svg width="22" height="22" viewBox="0 0 22 22"><path d="M14 3 6 11l8 8" stroke="#fff" stroke-width="1.6" fill="none"/></svg>
    <svg width="22" height="22" viewBox="0 0 22 22"><path d="M8 3l8 8-8 8" stroke="#fff" stroke-width="1.6" fill="none"/></svg>
    <svg width="22" height="22" viewBox="0 0 22 22"><path d="M8 8H4v12h14V8h-4M11 14V2M7 6l4-4 4 4" stroke="#fff" stroke-width="1.4" fill="none"/></svg>
    <svg width="26" height="22" viewBox="0 0 26 22"><path d="M13 4C10 2 6 2 2 3v15c4-1 8-1 11 1 3-2 7-2 11-1V3c-4-1-8-1-11 1zM13 4v15" stroke="#fff" stroke-width="1.4" fill="none"/></svg>
    <svg width="26" height="22" viewBox="0 0 26 22"><rect x="2" y="7" width="18" height="13" stroke="#fff" stroke-width="1.4" fill="none"/><path d="M6 7V3h18v13h-4" stroke="#fff" stroke-width="1.4" fill="none"/></svg>
  </nav>
</section>

<section class="screen screen--rev3" aria-label="Main screen, revision 3">
  <div class="status-bar">
    <span class="status-carrier"><span class="status-signal">●●●○○</span> Brightwave
      <svg width="12" height="9" viewBox="0 0 12 9"><path d="M1 3.2a7 7 0 0 1 10 0M2.8 5a4.5 4.5 0 0 1 6.4 0" stroke="#fff" stroke-width="1.3" fill="none"/><circle cx="6" cy="7.4" r="1.2" fill="#fff"/></svg>
    </span>
    <span class="status-time">4:21 PM</span>
    <span class="status-battery">100%
      <svg width="24" height="10" viewBox="0 0 24 10"><rect x=".5" y=".5" width="20" height="9" rx="2" fill="none" stroke="#fff"/><rect x="2" y="2" width="17" height="6" rx="1" fill="#fff"/><rect x="21.5" y="3" width="2" height="4" rx="1" fill="#fff"/></svg>
    </span>
  </div>
  <div class="address-bar">
    <div class="address-field">www.tutorpath.example.com
      <svg class="address-reload" width="18" height="18" viewBox="0 0 18 18"><path d="M14 9a5 5 0 1 1-1.5-3.6" stroke="#fff" stroke-width="1.4" fill="none"/><path d="M13.5 2.5v3.5H10" stroke="#fff" stroke-width="1.4" fill="none"/></svg>
    </div>
  </div>

  <div class="grant-strip">Get up to $5, 645* per year in Grants if you qualify</div>
  <div class="intro"><p>Complete our <em>3 minute</em> App!</p></div>
  <div class="banner banner--prompt">Select area of your interest</div>
  <div class="dot-rule"></div>

  <ul class="topics">
    <li class="topic"><span class="topic-icon topic-icon--round topic-icon--art"><svg width="18" height="18" viewBox="0 0 18 18"><path d="M14 2 7 10M5 11c-2 1-2 3-3 5 2-1 4-1 5-3" stroke="#fff" stroke-width="1.4" fill="none"/></svg></span><span class="topic-label">Art &amp; Design</span><span class="topic-go"><svg width="8" height="10" viewBox="0 0 8 10"><path d="M2 1l4 4-4 4" stroke="#fff" stroke-width="2" fill="none"/></svg></span></li>
    <li class="topic"><span class="topic-icon topic-icon--round topic-icon--business"><svg width="20" height="18" viewBox="0 0 20 18"><rect x="2" y="5" width="16" height="11" rx="1" stroke="#fff" stroke-width="1.4" fill="none"/><path d="M7 5V3h6v2M2 9h16" stroke="#fff" stroke-width="1.4" fill="none"/></svg></span><span class="topic-label">Business</span><span class="topic-go"><svg width="8" height="10" viewBox="0 0 8 10"><path d="M2 1l4 4-4 4" stroke="#fff" stroke-width="2" fill="none"/></svg></span></li>
    <li class="topic"><span class="topic-icon topic-icon--round topic-icon--justice"><svg width="20" height="20" viewBox="0 0 20 20"><rect x="6" y="2" width="10" height="5" transform="rotate(35 11 4.5)" fill="#fff"/><path d="M9 8 3 15" stroke="#fff" stroke-width="2"/><path d="M10 18h8" stroke="#fff" stroke-width="2"/></svg></span><span class="topic-label">Criminal Justice</span><span class="topic-go"><svg width="8" height="10" viewBox="0 0 8 10"><path d="M2 1l4 4-4 4" stroke="#fff" stroke-width="2" fill="none"/></svg></span></li>
    <li class="topic"><span class="topic-icon topic-icon--round topic-icon--education"><svg width="26" height="22" viewBox="0 0 26 22"><text x="13" y="9" text-anchor="middle" font-family="Roboto, sans-serif" font-size="9" fill="#fff">ABC</text><path d="M4 11h18" stroke="#fff"/><text x="13" y="20" text-anchor="middle" font-family="Roboto, sans-serif" font-size="9" fill="#fff">1 2 3</text></svg></span><span class="topic-label">Education &amp; Teaching</span><span class="topic-go"><svg width="8" height="10" viewBox="0 0 8 10"><path d="M2 1l4 4-4 4" stroke="#fff" stroke-width="2" fill="none"/></svg></span></li>
    <li class="topic"><span class="topic-icon topic-icon--round topic-icon--engineering"><svg width="20" height="20" viewBox="0 0 20 20"><circle cx="10" cy="3" r="1.6" stroke="#fff" fill="none"/><path d="M9 4.5 4 18M11 4.5 16 18M5.5 12h9" stroke="#fff" stroke-width="1.4" fill="none"/></svg></span><span class="topic-label">Engineering</span><span class="topic-go"><svg width="8" height="10" viewBox="0 0 8 10"><path d="M2 1l4 4-4 4" stroke="#fff" stroke-width="2" fill="none"/></svg></span></li>
    <li class="topic"><span class="topic-icon topic-icon--round topic-icon--other"><svg width="22" height="18" viewBox="0 0 22 18"><path d="M11 4C8 2 5 2 2 3v11c3-1 6-1 9 1 3-2 6-2 9-1V3c-3-1-6-1-9 1zM11 4v11" stroke="#fff" stroke-width="1.3" fill="none"/></svg></span><span class="topic-label">Other</span><span class="topic-go"><svg width="8" height="10" viewBox="0 0 8 10"><path d="M2 1l4 4-4 4" stroke="#fff" stroke-width="2" fill="none"/></svg></span></li>
  </ul>

  <nav class="toolbar" aria-label="Browser toolbar">
    <svg width="22" height="22" viewBox="0 0 22 22"><path d="M14 3 6 11l8 8" stroke="#fff" stroke-width="1.6" fill="none"/></svg>
    <svg width="22" height="22" viewBox="0 0 22 22"><path d="M8 3l8 8-8 8" stroke="#fff" stroke-width="1.6" fill="none"/></svg>
    <svg width="22" height="22" viewBox="0 0 22 22"><path d="M8 8H4v12h14V8h-4M11 14V2M7 6l4-4 4 4" stroke="#fff" stroke-width="1.4" fill="none"/></svg>
    <svg width="26" height="22" viewBox="0 0 26 22"><path d="M13 4C10 2 6 2 2 3v15c4-1 8-1 11 1 3-2 7-2 11-1V3c-4-1-8-1-11 1zM13 4v15" stroke="#fff" stroke-width="1.4" fill="none"/></svg>
    <svg width="26" height="22" viewBox="0 0 26 22"><rect x="2" y="7" width="18" height="13" stroke="#fff" stroke-width="1.4" fill="none"/><path d="M6 7V3h18v13h-4" stroke="#fff" stroke-width="1.4" fill="none"/></svg>
  </nav>
</section>

<p class="caption caption--rev2">Main Screen Revision 2</p>
<p class="caption caption--rev3">Main Screen Revision 3</p>

</body>
</html>
```